Business Cards Needed for Innovative Healthcare Marketing Company

We are a marketing company focused on healthcare. Our company is all about rebranding yourself renewing your image and generating results. The phoenix stands for "reborn" or "rising" which we provide new brands for our clients we take their old brands and renew it with creativity and innovation. I am looking for a business card with color dimension. I have attached an example of a card I think has the look and feel of what I am trying to accomplish. I like that the card example has black and grey font colors, I like the font placement and the small logo, I really like the use of the colors on the right those are the colors of my logo. My logo is phoenix so maybe incorporating flames similar to that design. I would like the back a solid color maybe red with an opaque version of the logo and website. As a marketing company I am always open to creative liberty!

Target Market(s)

Doctors and business professionals.

Industry/Entity Type

Marketing

Contact Information for Business Card

Valcorne Health Care Marketing
Marla Tenwick- CEO
#(512)638-2974
email-marla@valcorne.com
website- valcorne.com

Font styles to use
Sans Serif

Colors
ec1f27
f37122
ffc214
fbed22
fbf289
f04a50

Requirements
Must have
• The logo and required information
Nice to have
• icons by the information
Should not have
• child like font

```html
<!DOCTYPE html>
<html lang="en">
<head>
<meta charset="utf-8">
<title>Valcorne Health Care Marketing – Business Card</title>
<link href="https://fonts.googleapis.com/css2?family=Open+Sans:wght@300;400;600;700&display=swap" rel="stylesheet">
<style>
  :root {
    --stage: #262626;
    --card-white: #ffffff;
    --brand-red: #9e1e24;
    --brand-wine: #8f1d2c;
    --flame-orange: #f5952a;
    --flame-red: #d2381f;
    --flame-gold: #ffc214;
    --ink-light: #ffffff;
    --back-black: #000000;
  }
  * { box-sizing: border-box; margin: 0; padding: 0; }
  html, body {
    width: 1200px;
    height: 987px;
    overflow: hidden;
  }
  body {
    background: var(--stage);
    font-family: "Open Sans", Arial, sans-serif;
    position: relative;
  }
  .card {
    position: absolute;
    left: 293px;
    width: 615px;
    height: 352px;
    box-shadow: 0 4px 14px rgba(0,0,0,.55);
    overflow: hidden;
  }
  .card--front { top: 125px; background: var(--card-white); }
  .card--back { top: 511px; background: var(--back-black); }

  /* Front: brand block */
  .brand {
    position: absolute;
    display: flex;
    align-items: center;
    gap: 22px;
  }
  .brand--front { left: 135px; top: 52px; }
  .brand__mark {
    width: 104px;
    height: 104px;
    border-radius: 50%;
    background: var(--flame-red);
    flex: none;
  }
  .brand__name {
    color: var(--brand-wine);
    font-weight: 300;
    line-height: 1.05;
  }
  .brand__name-main { display: block; font-size: 42px; letter-spacing: 1px; }
  .brand__name-sub {
    display: block;
    font-size: 14px;
    letter-spacing: 1px;
    margin-top: 6px;
    padding-top: 5px;
    border-top: 1px solid #c9a6a9;
  }

  /* Front: red band */
  .contact-band {
    position: absolute;
    left: 0; right: 0; bottom: 0;
    height: 139px;
    background: var(--brand-red);
  }
  .contact-band::before {
    content: "";
    position: absolute;
    left: 0; right: 0; top: 0;
    height: 4px;
    background: linear-gradient(90deg, var(--brand-red), var(--flame-orange) 50%, var(--brand-red));
  }
  .person {
    position: absolute;
    right: 345px;
    top: 44px;
    text-align: right;
  }
  .person__name {
    color: var(--flame-orange);
    font-weight: 700;
    font-size: 22px;
    line-height: 1.2;
  }
  .person__title {
    color: var(--ink-light);
    font-weight: 700;
    font-size: 15px;
    line-height: 1.3;
  }
  .contact-list {
    position: absolute;
    left: 308px;
    top: 31px;
    list-style: none;
  }
  .contact-list__item {
    display: flex;
    align-items: center;
    gap: 9px;
    height: 23.5px;
    color: var(--ink-light);
    font-size: 16px;
  }
  .contact-list__icon { width: 14px; height: 14px; flex: none; fill: var(--flame-orange); }

  /* Back */
  .brand--back {
    left: 0; right: 0; top: 78px;
    flex-direction: column;
    gap: 18px;
  }
  .brand--back .brand__mark { width: 118px; height: 118px; }
  .brand--back .brand__name { text-align: center; color: var(--brand-wine); }
  .brand--back .brand__name-main { font-size: 38px; }
  .brand--back .brand__name-sub { font-size: 13px; border-top-color: #5a1a22; }
</style>
</head>
<body>
  <section class="card card--front" aria-label="Business card front">
    <div class="brand brand--front">
      <span class="brand__mark" aria-hidden="true"></span>
      <p class="brand__name">
        <span class="brand__name-main">VALCORNE</span>
        <span class="brand__name-sub">HEALTH CARE MARKETING</span>
      </p>
    </div>
    <div class="contact-band">
      <div class="person">
        <p class="person__name">Marla Tenwick</p>
        <p class="person__title">CEO</p>
      </div>
      <ul class="contact-list">
        <li class="contact-list__item">
          <svg class="contact-list__icon" viewBox="0 0 24 24" aria-hidden="true"><path d="M6.6 10.8a15.1 15.1 0 0 0 6.6 6.6l2.2-2.2a1 1 0 0 1 1-.25 11.4 11.4 0 0 0 3.6.57 1 1 0 0 1 1 1V20a1 1 0 0 1-1 1A17 17 0 0 1 3 4a1 1 0 0 1 1-1h3.5a1 1 0 0 1 1 1c0 1.25.2 2.45.57 3.57a1 1 0 0 1-.25 1z"/></svg>
          (512)638-2974
        </li>
        <li class="contact-list__item">
          <svg class="contact-list__icon" viewBox="0 0 24 24" aria-hidden="true"><path d="M2 5h20v14H2z M2 5l10 8 10-8" fill="var(--flame-orange)" stroke="var(--brand-red)" stroke-width="1.6" stroke-linejoin="round"/></svg>
          marla@valcorne.com
        </li>
        <li class="contact-list__item">
          <svg class="contact-list__icon" viewBox="0 0 24 24" aria-hidden="true"><circle cx="12" cy="12" r="10"/><path d="M2 12h20M12 2c3 3 3 17 0 20M12 2c-3 3-3 17 0 20" fill="none" stroke="var(--brand-red)" stroke-width="1.5"/></svg>
          www.valcorne.com
        </li>
      </ul>
    </div>
  </section>

  <section class="card card--back" aria-label="Business card back">
    <div class="brand brand--back">
      <span class="brand__mark" aria-hidden="true"></span>
      <p class="brand__name">
        <span class="brand__name-main">VALCORNE</span>
        <span class="brand__name-sub">HEALTH CARE MARKETING</span>
      </p>
    </div>
  </section>
</body>
</html>
```